Rollers & Glides.com

Vertical Business Card with focus on branding with our icon. Information on card will be logo, persons name, position, phone number, email address and website. Use the the name Marcus Pellow, position President, phone number 480.915.2267, email Marcus@rollersandglides-demo.com, website www.rollersandglides-demo.com.

```html
<!DOCTYPE html>
<html lang="en">
<head>
<meta charset="utf-8">
<title>Rollers &amp; Glides.com – Business Card</title>
<link rel="stylesheet" href="https://fonts.googleapis.com/css2?family=Oswald:wght@500&family=Roboto:wght@500&family=Arimo:wght@400&display=swap">
<style>
  :root {
    --stage: #0b0b0b;
    --card: #161616;
    --brand-blue: #3563b4;
    --name-blue: #1d74c9;
    --icon-blue: #1f78cf;
    --text-grey: #a3a3a3;
    --rule-grey: #8a8a8a;
  }
  * { margin: 0; padding: 0; box-sizing: border-box; }
  html, body {
    width: 1200px;
    height: 900px;
    overflow: hidden;
    background: var(--stage);
  }
  .canvas {
    width: 1200px;
    height: 900px;
    display: flex;
    flex-direction: column;
    align-items: center;
    justify-content: center;
    gap: 40px;
  }
  .card {
    width: 560px;
    height: 320px;
    background: var(--card);
    box-shadow: 0 6px 18px rgba(0, 0, 0, 0.6);
    position: relative;
  }
  /* Front face */
  .card-front {
    display: flex;
    align-items: center;
    justify-content: center;
  }
  .brand {
    display: flex;
    align-items: center;
    gap: 14px;
  }
  .brand-dot {
    width: 22px;
    height: 22px;
    border-radius: 50%;
    background: var(--brand-blue);
  }
  .brand-name {
    font-family: "Roboto", Arial, sans-serif;
    font-weight: 500;
    font-size: 30px;
    letter-spacing: 2px;
    color: var(--brand-blue);
  }
  /* Back face */
  .card-back {
    display: flex;
    align-items: center;
    justify-content: center;
    gap: 22px;
  }
  .identity {
    text-align: right;
  }
  .person-name {
    font-family: "Oswald", "Arial Narrow", sans-serif;
    font-weight: 500;
    font-size: 25px;
    line-height: 1;
    letter-spacing: -0.3px;
    text-transform: uppercase;
    color: var(--name-blue);
  }
  .person-role {
    font-family: "Arimo", Arial, sans-serif;
    font-size: 14px;
    color: var(--text-grey);
    margin-top: 3px;
    letter-spacing: 0.5px;
  }
  .divider {
    width: 1px;
    height: 78px;
    background: var(--rule-grey);
    margin-top: 22px;
  }
  .contact {
    list-style: none;
    margin-top: 32px;
    font-family: "Arimo", Arial, sans-serif;
    font-size: 13px;
    color: var(--text-grey);
  }
  .contact-item {
    display: flex;
    align-items: center;
    gap: 7px;
    line-height: 19px;
  }
  .contact-icon {
    width: 13px;
    height: 13px;
    flex: none;
    fill: var(--icon-blue);
  }
</style>
</head>
<body>
  <main class="canvas">
    <section class="card card-front" aria-label="Card front">
      <div class="brand">
        <span class="brand-dot"></span>
        <span class="brand-name">Rollers &amp; Glides.com</span>
      </div>
    </section>

    <section class="card card-back" aria-label="Card back">
      <div class="identity">
        <h1 class="person-name">Marcus Pellow</h1>
        <p class="person-role">President</p>
      </div>
      <span class="divider"></span>
      <ul class="contact">
        <li class="contact-item">
          <svg class="contact-icon" viewBox="0 0 16 16" aria-hidden="true">
            <path d="M3.6 1.2l2.3 2.6-1.3 1.9c.9 2 2.6 3.8 4.7 4.8l1.9-1.3 2.6 2.3-1.3 2.6C7.7 14.6 1.4 8.3 1 3.5z"/>
          </svg>
          480.915.2267
        </li>
        <li class="contact-item">
          <svg class="contact-icon" viewBox="0 0 16 16" aria-hidden="true">
            <path d="M1 3h14v1.2L8 8.8 1 4.2z M1 5.6l7 4.6 7-4.6V13H1z"/>
          </svg>
          Marcus@rollersandglides-demo.com
        </li>
        <li class="contact-item">
          <svg class="contact-icon" viewBox="0 0 16 16" aria-hidden="true">
            <path d="M8 1a7 7 0 1 0 0 14A7 7 0 0 0 8 1zm0 1.3c.8 0 1.7 1.5 2 3.7H6c.3-2.2 1.2-3.7 2-3.7zM5.9 2.8C5.2 3.7 4.8 4.8 4.7 6H2.6a5.7 5.7 0 0 1 3.3-3.2zm4.2 0A5.7 5.7 0 0 1 13.4 6h-2.1c-.1-1.2-.5-2.3-1.2-3.2zM2.4 7.3h2.2v1.4H2.4zm3.5 0h4.2v1.4H5.9zm5.5 0h2.2v1.4h-2.2zM2.6 10h2.1c.1 1.2.5 2.3 1.2 3.2A5.7 5.7 0 0 1 2.6 10zm3.4 0h4c-.3 2.2-1.2 3.7-2 3.7s-1.7-1.5-2-3.7zm5.3 0h2.1a5.7 5.7 0 0 1-3.3 3.2c.7-.9 1.1-2 1.2-3.2z"/>
          </svg>
          www.rollersandglides-demo.com
        </li>
      </ul>
    </section>
  </main>
</body>
</html>
```